Blood Testing Health App

We are looking for a graphics designer to create a web app for us so that we may insert it into a health management website system.
For branding purposes we are at www.Vantiqor.com and we are revamping our website... Example of new colors attached.
How we work...
We are a blood testing company based in the USA.
We offer a blood testing service nationwide in the USA.
We allow customers to order tests directly from us, visit a lab, have their blood drawn, or submit a urine sample, the lab tests it and they send the results back to our computer system and we share it with the customer.
The benefits of this are the customer does not need to go to the doctor and pay for the doctors visit to order these tests, which save them money. The tests are cheaper than going through the doctor. The customer simply uses us to get the test and the results and they can then take the results to their doctor... this process has saved them money. Others may be interested in regular check ups for blood work etc... and this allows them to do it with out needing a doctor, or if you have no insurance, this is a cheaper option too. We are quicker than a doctor, customers do not need appointments etc.
Hopefully you now have a better understanding as to what we do.
Here is the spec.
The app screen size is 750 px wide by 700 px high. ( A pdf is attached to show where the app is going to go, it is on page 3 of the pdf) The customer will have the ability to scroll… therefore the length of the page can be longer.
The app will consist of the following sections
Entry Page –
This will be the first page the user sees upon opening the app. This will be where they are directed from to the sections of the app discussed below. This needs to be branded for VantiQor with a modern look.
1 – Order Test (Giving them the ability to purchase a blood test within the app)
2 – VantiQor Dashboard (A dashboard that has everything they could need to use our service_
How it works Section on entry page – this will be a simple set of graphics showing how the service works. We already have the graphics for this, they do not need to be built again. They are attached to this brief
Basic structure of sections –
Order Test –
This page contains all tests, filed in categories – and Sub categories – Each test needs a link to an Information section – Price – Buy Now – Cart Process
VantiQor Dashboard –
A page of icons along the top of the app
- My Confirmation
- My Nearest Lab
- My Receipt
- My Orders
- My Account
- My Results
- My Inbox
- Contact Us
Sections in more detail -
Order A Test –
Show all categories/ sub categories – There are 23 categories, 14 sub categories, and within these categories are 300 tests - Here is the information for the categories etc - http://www.vantiqor.com/panels.aspx?PanelGroupID=4 Just in case it helps :)
We need to present this in a graphic format that is spacious, modern (brimlake, kivvo web appearance is the direction we are going for) We need it to be clear and not overwhelming to the customer.
Functionality idea…
Customer clicks category/ subcategory and tests appear.
Customer sees small 35 word description. For more information the test opens into a lightbox or expand the container which ever graphic designer believes to be most visually appealing
Buy Now must always be visible, along with price of the test
Buying process explained – Customer clicks buy now –
They are then taken to a Review Order screen ( This contains Order summary and choose payment method – insert payment details )
– Confirm payment –
Confirmation screen appears, thanking them.
They are then taken to the VantiQor Dashboard...
VantiQor Dashboard –
"My Confirmation" - Print Confirmation Order (PDF is in brief, we want this web based not a pdf download)
"My Nearest Lab Location" - This does not need to be designed because the web developer has this part under control, but we do need the icon in the dashboard
"My Receipt" - Print receipt - This does not exist in our system yet. So we need to create this from scratch - It will need to have - The test they are purchasing and the amount of the test - The customers name - The order ID - Must provide printer friendly option too
"My Orders" - This will have a list of orders - At the end of each order will be a status update of either "Test results" "Open order"
A graphic table format would be perfect. This will be linked to relevant results if they have been received. I have also attached a version of what the customer currently sees on our website. We know it is nasty ;) We are redesigning... but the information is there for this section to help design it with the right info. If the results are ready it will say in this list.
"Results Ready" will be a link to show those results once the customer has clicked the link, and the results will appear in the app, under the icons. There must be a printer friendly version too.
"My Results" Developer will sort this page out but we need the icon... It will be exactly like my orders but only show test results
"My Account" - This will be a place for them to update their personal information - Name, DOB, Address, Email Address
"My Inbox" - An inbox interface - Our way of contacting the customer for promotions we are running etc – We need a design of how this screen will appear. We also need the icon in the dashboard to have a notification on it if there are messages in the customers inbox. A little red 1, or circle with number of messages in the inbox.
"Customer Service" - This does not need to be designed because the web developer has this part under control, but we do need the icon in the dashboard
Icons appear along the top of app ( example - Mac icons/ iphone app icons) When the customer clicks an icon the content always appears below the icons
Here is more information for the icons and what should appear when each icon is clicked.
Screens to be designed –
Entry Page
Order A Test Page
Review Order Screen/Payment Screen - Show a lightbox that shows payment has been confirmed. Customer clicks close and are on the Confirmation Screen
VantiQor Dashboard - Screens mentioned in detail above
We can't wait to see your designs!
Please email any questions.
Hi all this is the first time we have used pixel harbor and understand the budget was too low for this project. We have now increased the budget to $2,000 and extended the deadline by another week
Hi all we are receiving some really great designs. I just added an example of the space that the web app will be going into... It is called "morvelapp.pdf"
Hi guys updated the brief. Hopefully this will help with the dashboard part of the design

```html
<!DOCTYPE html>
<html lang="en">
<head>
<meta charset="utf-8">
<title>VantiQor Dashboard – My Orders</title>
<link rel="stylesheet" href="https://fonts.googleapis.com/css2?family=Open+Sans:wght@300;400;600;700&display=swap">
<style>
:root{
  --green:#7dc13a;
  --green-dark:#5fa224;
  --slate:#545a54;
  --panel:#e8e8e8;
  --band-top:#f4f4f4;
  --band-bottom:#dcdcdc;
  --ink:#2b2b2b;
  --muted:#8a8a8a;
  --link:#e8501c;
  --active:#1f6fb8;
  --badge:#f04e23;
  --white:#ffffff;
  --icon-dark:#5a5a5a;
}
*{box-sizing:border-box;margin:0;padding:0}
html,body{width:1068px;height:1200px;overflow:hidden;background:var(--white)}
body{font-family:"Open Sans",Arial,sans-serif;color:var(--ink)}
.app{position:absolute;left:0;top:0;width:750px;height:842px;transform:scale(1.424);transform-origin:0 0;background:var(--white)}

/* header */
.brand{position:absolute;left:18px;top:46px;display:flex;align-items:center;gap:10px}
.brand-mark{width:26px;height:26px;background:var(--green)}
.brand-name{font-size:40px;font-weight:400;color:#2f2f2f;letter-spacing:1px;line-height:1}
.tab{position:absolute;top:30px;height:71px;width:124px;text-align:center;font-size:11px;letter-spacing:.3px}
.tab svg{display:block;margin:12px auto 6px}
.tab-order{left:338px;color:var(--muted)}
.tab-dash{left:456px;background:#ececec;border-radius:10px 10px 0 0;color:var(--green-dark)}
.social{position:absolute;top:63px;display:flex;gap:10px;left:627px}
.social span{width:29px;height:29px;border-radius:50%;background:var(--green);display:block}

/* icon band */
.band{position:absolute;left:0;top:101px;width:750px;height:135px;background:linear-gradient(var(--band-top),var(--band-bottom));border-top:1px solid #e2e2e2}
.nav{position:absolute;top:0;width:92px;text-align:center;font-size:11.5px;line-height:1.1;color:#333}
.nav .disc{width:62px;height:62px;margin:28px auto 6px;border-radius:50%;background:radial-gradient(circle at 50% 35%,#ffffff,#d6d6d6);border:1px solid #c4c4c4;box-shadow:0 2px 3px rgba(0,0,0,.25);display:flex;align-items:center;justify-content:center;position:relative}
.nav.active{color:var(--active)}
.badge{position:absolute;right:-4px;top:-7px;background:var(--badge);color:#fff;font-size:10px;font-weight:700;border-radius:4px;padding:1px 6px}
.pointer{position:absolute;left:224px;top:228px;width:0;height:0;border-left:8px solid transparent;border-right:8px solid transparent;border-bottom:8px solid var(--white)}

/* panels */
.panel{position:absolute;left:17px;top:262px;width:712px;height:381px;background:var(--panel);border-radius:6px}
.card{position:absolute;left:11px;width:689px;background:var(--white);border-radius:8px;overflow:hidden}
.card-head{height:47px;background:var(--green);color:#fff;font-size:19px;font-weight:300;padding:12px 15px;letter-spacing:.3px}
.cols{height:37px;background:var(--slate);color:#fff;font-size:13px;position:relative}
.row{height:35px;position:relative;font-size:11px;border-bottom:1px solid #e6e6e6}
.row:last-child{border-bottom:none}
.cols span,.row span{position:absolute;top:50%;transform:translateY(-50%);white-space:nowrap}
.row .link{color:var(--link)}

/* notes */
.notes{position:absolute;left:27px;top:661px;width:700px;font-size:11.2px;line-height:1.36;color:#333}
.notes p{margin-bottom:12px}
</style>
</head>
<body>
<div class="app">
  <header>
    <div class="brand"><span class="brand-mark"></span><span class="brand-name">VANTIQOR</span></div>
    <div class="tab tab-order">
      <svg width="22" height="18" viewBox="0 0 22 18"><rect x="2" y="1" width="18" height="12" rx="1.5" fill="#9a9a9a"/><rect x="0" y="14" width="22" height="3" rx="1" fill="#9a9a9a"/></svg>
      ORDER A TEST
    </div>
    <div class="tab tab-dash">
      <svg width="24" height="22" viewBox="0 0 24 22"><rect x="7" y="1" width="16" height="13" fill="none" stroke="#5fa224" stroke-width="2"/><rect x="1" y="7" width="16" height="13" fill="#fff" stroke="#5fa224" stroke-width="2"/><rect x="1" y="7" width="16" height="3" fill="#5fa224"/></svg>
      DASHBOARD
    </div>
    <div class="social" aria-label="Social links"><span></span><span></span><span></span></div>
  </header>

  <nav class="band">
    <div class="nav" style="left:0">
      <div class="disc"><svg width="34" height="30" viewBox="0 0 34 30"><rect x="3" y="2" width="28" height="20" rx="2" fill="none" stroke="var(--icon-dark)" stroke-width="3"/><polyline points="7,13 12,13 15,7 18,18 21,11 27,11" fill="none" stroke="var(--icon-dark)" stroke-width="2"/><rect x="12" y="24" width="10" height="4" fill="var(--icon-dark)"/></svg></div>My<br>Confirmation</div>
    <div class="nav" style="left:93px">
      <div class="disc"><svg width="30" height="34" viewBox="0 0 30 34"><rect x="12" y="3" width="6" height="16" rx="1" fill="var(--icon-dark)" transform="rotate(-25 15 11)"/><path d="M8 24 Q20 24 22 14" fill="none" stroke="var(--icon-dark)" stroke-width="3"/><rect x="4" y="28" width="22" height="4" fill="var(--icon-dark)"/></svg></div>My<br>Nearest Lab</div>
    <div class="nav active" style="left:186px">
      <div class="disc"><svg width="24" height="36" viewBox="0 0 24 36"><path d="M5 2 C5 12 19 14 19 20 S5 28 5 34" fill="none" stroke="#3a7ab8" stroke-width="3"/><path d="M19 2 C19 12 5 14 5 20 S19 28 19 34" fill="none" stroke="#3a7ab8" stroke-width="3"/><g stroke="#3a7ab8" stroke-width="2"><line x1="7" y1="6" x2="17" y2="6"/><line x1="9" y1="11" x2="15" y2="11"/><line x1="9" y1="25" x2="15" y2="25"/><line x1="7" y1="30" x2="17" y2="30"/></g></svg></div>My Orders</div>
    <div class="nav" style="left:281px">
      <div class="disc"><svg width="28" height="34" viewBox="0 0 28 34"><rect x="2" y="4" width="24" height="28" rx="2" fill="none" stroke="var(--icon-dark)" stroke-width="3"/><rect x="9" y="1" width="10" height="6" fill="var(--icon-dark)"/><polyline points="6,19 10,19 12,13 15,25 18,16 22,16" fill="none" stroke="var(--icon-dark)" stroke-width="2"/></svg></div>My Results</div>
    <div class="nav" style="left:373px">
      <div class="disc"><svg width="28" height="34" viewBox="0 0 28 34"><rect x="2" y="4" width="24" height="28" rx="2" fill="none" stroke="var(--icon-dark)" stroke-width="3"/><rect x="9" y="1" width="10" height="6" fill="var(--icon-dark)"/><g fill="var(--icon-dark)"><rect x="6" y="11" width="3" height="3"/><rect x="11" y="11" width="11" height="3"/><rect x="6" y="17" width="3" height="3"/><rect x="11" y="17" width="11" height="3"/><rect x="6" y="23" width="3" height="3"/><rect x="11" y="23" width="11" height="3"/></g></svg></div>My Receipts</div>
    <div class="nav" style="left:466px">
      <div class="disc" style="background:radial-gradient(circle at 50% 35%,#6a6a6a,#3f3f3f)"><svg width="34" height="36" viewBox="0 0 34 36"><circle cx="17" cy="11" r="8" fill="#2e2e2e"/><path d="M3 36 Q3 21 17 21 Q31 21 31 36Z" fill="#2e2e2e"/></svg></div>My Account</div>
    <div class="nav" style="left:560px">
      <div class="disc"><svg width="36" height="26" viewBox="0 0 36 26"><rect x="1" y="1" width="34" height="24" rx="2" fill="var(--icon-dark)"/><polyline points="2,3 18,15 34,3" fill="none" stroke="#d9d9d9" stroke-width="2"/></svg><span class="badge">2</span></div>My Inbox</div>
    <div class="nav" style="left:653px">
      <div class="disc" style="background:radial-gradient(circle at 50% 35%,#6a6a6a,#3f3f3f)"><svg width="34" height="36" viewBox="0 0 34 36"><circle cx="17" cy="12" r="8" fill="#2e2e2e"/><path d="M8 12 A9 9 0 0 1 26 12" fill="none" stroke="#222" stroke-width="2"/><path d="M3 36 Q3 22 17 22 Q31 22 31 36Z" fill="#2e2e2e"/></svg></div>Contact Us</div>
    <span class="pointer" style="top:127px"></span>
  </nav>

  <main class="panel">
    <section class="card" style="top:16px;height:128px">
      <div class="card-head">ORDERS</div>
      <div class="cols"><span style="left:15px">First Name</span><span style="left:123px">Last Name</span><span style="left:231px">Order ID</span><span style="left:327px">Date/Time Created</span></div>
      <div class="row"><span style="left:16px">Dana</span><span style="left:123px">Whitlow</span><span style="left:231px">34584</span><span style="left:329px">7/9/2013 12:37:00 PM</span><span class="link" style="left:475px">View Test Results</span><span class="link" style="left:599px">Email Results</span></div>
    </section>

    <section class="card" style="top:168px;height:198px">
      <div class="card-head">YOUR ORDER HISTORY</div>
      <div class="cols"><span style="left:15px">Order ID</span><span style="left:106px">Creation DateTime</span><span style="left:275px">Order Status</span></div>
      <div class="row"><span style="left:16px">34584</span><span style="left:107px">9/23/2013 12:37:00 PM</span><span style="left:274px">SENT TO LABRIVO</span><span class="link" style="left:420px">View Results</span></div>
      <div class="row"><span style="left:16px">35877</span><span style="left:111px">8/16/2013 12:54:00 AM</span><span style="left:274px">SENT TO LABRIVO</span><span class="link" style="left:421px">View Results</span><span style="left:516px">TRA Questionnaire</span></div>
      <div class="row"><span style="left:16px">36195</span><span style="left:111px">8/26/2013 12:54:00 AM</span><span style="left:274px">SENT TO LABRIVO</span><span class="link" style="left:421px">View Results</span></div>
    </section>
  </main>

  <footer class="notes">
    <p>Folio Reader is required to view your lab results. If you do not yet have Folio Reader, you can get it by clicking here and following the instructions.</p>
    <p><b>PLEASE NOTE:</b> Orders which are in 'PENDING' mode have not been charged to your credit card or Paywell account.<br>They have not been accepted by Payw and can be regarded as incomplete.</p>
    <p>You must bring your Lab Order to your nearest Labrivo Patient Service Center in order to obtain your lab work. Please click the link below, print the order and bring it with you when you have your blood drawn.</p>
    <p><b>CRITICAL NOTICE:</b> The Crestview Browser is not currently able to download and/or print our lab order. All other browsers function correctly. If you are using Crestview, please exit and login with another browser in order to download, view and print the lab order.</p>
  </footer>
</div>
</body>
</html>
```